Business Card for my New Brokerage

Looking to get a business card design for my new Real Estate Brokerage.
I want it with Picture, Phone Number, Email, Website, Office Address
Name and Designation. Please add logo too.

Target Market(s)

Real Estate Investors or Home Buyers

Industry/Entity Type

Real Estate

Contact Information for Business Card

Name, Email, Phone Number, website, email, office address

Colors
EB3D1F
EC4F4E
F09395
F8D3D4
FCEDEE

Requirements
Must have
• Minimalistic, Clean, Modern, Photo
Nice to have
• White and Red Colors

```html
<!DOCTYPE html>
<html lang="en">
<head>
<meta charset="utf-8">
<title>Ember Realty Inc – Business Card</title>
<link rel="stylesheet" href="https://fonts.googleapis.com/css2?family=Montserrat:wght@800&family=Arimo:wght@400&display=swap">
<style>
  :root {
    --stage: #c9c9c9;
    --card: #2b2b2b;
    --red: #e30613;
    --white: #f2f2f2;
    --muted: #d9d9d9;
    --photo-dark: #2e2e2e;
    --photo-mid: #3e3a38;
  }
  * { box-sizing: border-box; margin: 0; padding: 0; }
  html, body {
    width: 1200px; height: 800px; overflow: hidden;
    background: var(--stage);
    font-family: "Arimo", Arial, sans-serif;
  }
  .stage {
    width: 1200px; height: 800px;
    display: flex; align-items: center; justify-content: center; gap: 40px;
  }
  .card {
    position: relative;
    width: 540px; height: 309px;
    background: var(--card);
    border: 2px solid var(--red);
    overflow: hidden;
  }

  /* Brand name */
  .brand {
    display: flex; align-items: center; gap: 8px;
    font-family: "Montserrat", Arial, sans-serif;
    font-weight: 800;
    color: var(--red);
    letter-spacing: 0.5px;
    text-transform: uppercase;
    white-space: nowrap;
  }
  .brand-mark { width: 9px; height: 9px; background: var(--red); flex: none; }

  /* Info side */
  .card--info .brand {
    position: absolute; right: 44px; top: 36px; font-size: 24px;
  }
  .person {
    position: absolute; left: 34px; top: 112px;
  }
  .person-name {
    font-family: "Montserrat", Arial, sans-serif;
    font-weight: 800; font-size: 20px; color: var(--red);
    text-transform: uppercase; letter-spacing: 0.3px;
  }
  .person-title {
    font-size: 15px; color: var(--muted); margin-top: 3px;
  }
  .divider {
    position: absolute; left: 34px; right: 34px; top: 172px;
    height: 1px; background: var(--red);
  }
  .contacts {
    position: absolute; left: 34px; top: 188px;
    list-style: none;
  }
  .contacts li {
    display: flex; align-items: center; gap: 8px;
    font-size: 14px; color: var(--white); line-height: 24px;
  }
  .contacts svg { width: 13px; height: 13px; flex: none; }
  .accent { color: var(--red); }
  .address {
    position: absolute; right: 34px; top: 192px;
    font-size: 14px; line-height: 22px; color: var(--white);
    font-style: normal;
  }

  /* Photo side */
  .card--photo .brand {
    position: absolute; left: 36px; bottom: 48px; font-size: 20px;
  }
  .portrait {
    position: absolute; right: 0; top: 0; bottom: 0; width: 42%;
    background: linear-gradient(180deg, var(--photo-dark) 0%, var(--photo-mid) 55%, #1f1f1f 100%);
  }
</style>
</head>
<body>
<main class="stage">

  <section class="card card--info" aria-label="Business card front">
    <div class="brand"><span>Ember Realty Inc</span><span class="brand-mark"></span></div>

    <div class="person">
      <h1 class="person-name">Marcus Hale</h1>
      <p class="person-title">Managing Director</p>
    </div>

    <div class="divider"></div>

    <ul class="contacts">
      <li>
        <svg viewBox="0 0 16 16" aria-hidden="true"><path fill="#e30613" d="M3.6 1.5 6 4l-1.4 1.6a9 9 0 0 0 5.8 5.8L12 10l2.5 2.4-1.6 2.1C7.4 14.2 1.8 8.6 1.5 3.1z"/></svg>
        <span>044-555 210 377</span>
      </li>
      <li>
        <svg viewBox="0 0 16 16" aria-hidden="true"><rect x="1" y="3" width="14" height="10" fill="#e30613"/><path d="M1 3l7 6 7-6" fill="none" stroke="#2b2b2b" stroke-width="1.4"/></svg>
        <span>hello@emberrealty.com</span>
      </li>
      <li>
        <svg viewBox="0 0 16 16" aria-hidden="true"><g fill="none" stroke="#e30613" stroke-width="1.4"><circle cx="8" cy="8" r="6.3"/><ellipse cx="8" cy="8" rx="2.8" ry="6.3"/><path d="M1.7 8h12.6M3 4.5h10M3 11.5h10"/></g></svg>
        <span>www.<span class="accent">emberrealty</span>.com</span>
      </li>
    </ul>

    <address class="address">88, Harbor Lane Suite 400<br>30217, Westbrook</address>
  </section>

  <section class="card card--photo" aria-label="Business card back">
    <div class="brand"><span>Ember Realty Inc</span><span class="brand-mark"></span></div>
    <div class="portrait" role="img" aria-label="Portrait photo of the agent in a dark suit and tie"></div>
  </section>

</main>
</body>
</html>
```